Pepper & Palm Business Card FUN & EXCITING

Here is the Information for the Card:
Jaswinder Bains (Ravi)
E: RaviBains@postlark.com
C: (480) 555-0147
www.PepperPalmLV.com

We don't want traditional Indian cliche, We a playful bold and fun business card.

Files: https://files.cloudvessel.net/share/folders/7TqRmXpZ2vKa9LwBn4YcHd3JsEf6UoGi?usp=share_link

https://files.cloudvessel.net/share/folders/4MzXaQ8rTw2YbNcVk6PsLe5GhJdR3FoU?usp=share_link

Target Market(s)

Las Vegas Local Restaurant

Industry/Entity Type

Indian Restaurant

Contact Information for Business Card

Name, Email, Cell Phone, Company Logo

```html
<!DOCTYPE html>
<html lang="en">
<head>
<meta charset="utf-8">
<title>Pepper &amp; Palm Business Card</title>
<link rel="stylesheet" href="https://fonts.googleapis.com/css2?family=Montserrat:wght@400;600;700;800&display=swap">
<style>
  :root {
    --backdrop: #2b2b2b;
    --card: #1d1d1d;
    --accent: #e8812f;
    --ink: #ffffff;
    --art-warm: #e9a25a;
    --art-cream: #f3e6cf;
  }
  * { margin: 0; padding: 0; box-sizing: border-box; }
  html, body { width: 1200px; height: 1108px; overflow: hidden; }
  body {
    background: var(--backdrop);
    font-family: "Montserrat", sans-serif;
    color: var(--ink);
    position: relative;
  }
  .card {
    position: absolute;
    left: 257px;
    width: 697px;
    background: var(--card);
    border-radius: 18px;
    box-shadow: 0 6px 14px rgba(0,0,0,0.35);
  }
  .card-front { top: 128px; height: 426px; }
  .card-back { top: 595px; height: 440px; }

  .front-brand {
    position: absolute;
    left: 0; right: 0;
    top: 180px;
    text-align: center;
    font-weight: 800;
    font-size: 54px;
    letter-spacing: 0.5px;
    color: var(--ink);
  }

  .back-brand {
    position: absolute;
    left: 142px;
    top: 180px;
    width: 110px;
    text-align: center;
  }
  .back-brand-name {
    font-weight: 800;
    font-size: 21px;
    line-height: 1.05;
    color: var(--ink);
  }
  .back-brand-art {
    display: block;
    margin: 8px auto 0;
    width: 96px;
    height: 58px;
    border-radius: 10px;
    background: linear-gradient(135deg, var(--art-cream), var(--art-warm));
  }
  .back-brand-tagline {
    margin-top: 4px;
    font-size: 6px;
    color: var(--ink);
  }

  .divider {
    position: absolute;
    left: 299px;
    top: 170px;
    width: 2px;
    height: 131px;
    background: var(--accent);
  }
  .contact {
    position: absolute;
    left: 312px;
    top: 170px;
  }
  .contact-name {
    font-weight: 600;
    font-size: 26px;
    color: var(--accent);
    margin-bottom: 16px;
  }
  .contact-list { list-style: none; }
  .contact-item {
    display: flex;
    align-items: center;
    font-size: 16px;
    font-weight: 400;
    height: 30px;
  }
  .contact-icon {
    width: 14px;
    height: 14px;
    margin-right: 22px;
    fill: var(--accent);
  }
</style>
</head>
<body>
  <section class="card card-front">
    <div class="front-brand">Pepper &amp; Palm</div>
  </section>

  <section class="card card-back">
    <div class="back-brand">
      <div class="back-brand-name">Pepper &amp; Palm</div>
      <div class="back-brand-art" role="img" aria-label="Playful cartoon mascot of a curry bowl and naan walking together"></div>
      <div class="back-brand-tagline">"Fresh from our kitchen"</div>
    </div>

    <div class="divider"></div>

    <div class="contact">
      <div class="contact-name">Jaswinder Bains (Ravi)</div>
      <ul class="contact-list">
        <li class="contact-item">
          <svg class="contact-icon" viewBox="0 0 16 16" aria-hidden="true"><path d="M2 5c0-2 2-3 6-3s6 1 6 3v1h-3V4.5H5V6H2z M4 7h8l2 6H2z"/></svg>
          (480) 555-0147
        </li>
        <li class="contact-item">
          <svg class="contact-icon" viewBox="0 0 16 16" aria-hidden="true"><path d="M1 3h14v1L8 9 1 4z M1 6l7 5 7-5v7H1z"/></svg>
          RaviBains@postlark.com
        </li>
        <li class="contact-item">
          <svg class="contact-icon" viewBox="0 0 16 16" aria-hidden="true"><circle cx="8" cy="8" r="7"/></svg>
          www.PepperPalmLV.com
        </li>
      </ul>
    </div>
  </section>
</body>
</html>
```